Local Flower Farm Needs Business Card Design

I need business cards designed for a flower farm based in Eudora, Kansas.
Business Info:
We are a local cut flower farm located in Eudora, Kansas, founded by Corinne Haldwick. What started as a passion for agriculture and search for more joy in daily life has blossomed into a small business dedicated to providing the community with beautiful, fresh, and sustainable flowers. We specialize in local, seasonal blooms, ensuring that every petal reflects the care and dedication we pour into our craft. Our mission is to deliver the highest quality flowers directly to our customers through local farmers markets and to florists who share our commitment to sustainability. Join us in celebrating the beauty of nature, one bloom at a time!
Contact Details:
Corinne Haldwick
Owner
Phone 913-555-0147
Facebook: Rosalind Thorpe Gardens
Instagram: @RosalindThorpeGardens
Website: RosalindThorpeGardens.example
Target Market(s)
Wholesale to Florists and Direct to Consumer via Farmers Market
Industry/Entity Type
Florist, Farm
Contact Information for Business Card
Name, Contact Info, Logo
Look and feel
Each slider illustrates characteristics of the customer's brand and the style your logo design should communicate.

```html
<!DOCTYPE html>
<html lang="en">
<head>
<meta charset="utf-8">
<title>Rosalind Thorpe Gardens – Business Card</title>
<link rel="stylesheet" href="https://fonts.googleapis.com/css2?family=Playfair+Display:wght@400;700&family=Tinos&display=swap">
<style>
  :root {
    --teal-deep: #0b2a30;
    --teal-mid: #12414a;
    --teal-soft: #1d5a63;
    --paper: #ffffff;
    --stage: #e9ecec;
  }
  * { box-sizing: border-box; margin: 0; padding: 0; }
  html, body { width: 1200px; height: 901px; overflow: hidden; }
  body {
    background: var(--stage);
    position: relative;
    font-family: "Tinos", "Times New Roman", serif;
    color: var(--teal-deep);
  }
  .card {
    position: absolute;
    left: 240px;
    width: 720px;
    height: 411px;
    border-radius: 22px;
    overflow: hidden;
  }
  .card--back { top: 28px; background: var(--teal-deep); }
  .card--front { top: 462px; background: var(--paper); box-shadow: 0 2px 10px rgba(0,0,0,.12); }

  /* back side brand seal */
  .seal-back {
    position: absolute;
    left: 50%; top: 50%;
    width: 250px; height: 250px;
    transform: translate(-50%, -50%);
    border: 1.5px solid var(--teal-soft);
    border-radius: 50%;
    display: flex; align-items: center; justify-content: center;
    text-align: center;
  }
  .seal-back .brand-name {
    font-family: "Playfair Display", Georgia, serif;
    font-weight: 400;
    font-size: 30px;
    line-height: 1.15;
    color: var(--teal-soft);
  }

  /* front side brand seal */
  .seal-front {
    position: absolute;
    left: 55px; top: 28px;
    width: 230px; height: 230px;
    border: 1.5px solid var(--teal-deep);
    border-radius: 50%;
    display: flex; align-items: center; justify-content: center;
    text-align: center;
  }
  .seal-front .brand-name {
    font-family: "Playfair Display", Georgia, serif;
    font-weight: 400;
    font-size: 28px;
    line-height: 1.15;
    color: var(--teal-deep);
  }

  .owner {
    position: absolute;
    right: 42px; top: 62px;
    text-align: right;
  }
  .owner__name {
    font-family: "Playfair Display", Georgia, serif;
    font-weight: 700;
    font-size: 32px;
    letter-spacing: .3px;
  }
  .owner__role {
    font-size: 17px;
    margin-top: 2px;
  }
  .edge-tab {
    position: absolute;
    right: 0; top: 72px;
    width: 10px; height: 46px;
    background: var(--teal-deep);
  }

  .feature-mark {
    position: absolute;
    right: 30px; bottom: 22px;
    width: 250px; height: 230px;
    display: flex; align-items: center; justify-content: flex-end;
    text-align: right;
  }
  .feature-mark .brand-name {
    font-family: "Playfair Display", Georgia, serif;
    font-weight: 700;
    font-size: 46px;
    line-height: 1.05;
    color: var(--teal-deep);
  }

  .contacts {
    position: absolute;
    left: 48px; top: 275px;
    list-style: none;
  }
  .contacts li {
    display: flex; align-items: center;
    font-size: 19px;
    height: 28px;
  }
  .contacts .icon {
    width: 18px; height: 18px;
    margin-right: 10px;
    flex: none;
  }
  .contacts .icon--plain {
    display: inline-block;
    width: 15px; height: 15px;
    margin: 0 12px 0 2px;
    background: var(--teal-mid);
    border-radius: 3px;
    flex: none;
  }
</style>
</head>
<body>

<section class="card card--back" aria-label="Card back">
  <div class="seal-back">
    <p class="brand-name">Rosalind<br>Thorpe<br>Gardens</p>
  </div>
</section>

<section class="card card--front" aria-label="Card front">
  <div class="seal-front">
    <p class="brand-name">Rosalind<br>Thorpe<br>Gardens</p>
  </div>

  <div class="owner">
    <p class="owner__name">Corinne Haldwick</p>
    <p class="owner__role">Owner</p>
  </div>
  <div class="edge-tab"></div>

  <div class="feature-mark">
    <p class="brand-name">Rosalind<br>Thorpe<br>Gardens</p>
  </div>

  <ul class="contacts">
    <li>
      <svg class="icon" viewBox="0 0 24 24" aria-hidden="true">
        <path d="M6.6 10.8a15 15 0 0 0 6.6 6.6l2.2-2.2c.3-.3.7-.4 1-.2 1.1.4 2.3.6 3.6.6.6 0 1 .4 1 1V20c0 .6-.4 1-1 1A17 17 0 0 1 3 4c0-.6.4-1 1-1h3.5c.6 0 1 .4 1 1 0 1.3.2 2.5.6 3.6.1.3 0 .7-.2 1z" fill="var(--teal-deep)"/>
      </svg>
      913-555-0147
    </li>
    <li>
      <svg class="icon" viewBox="0 0 24 24" aria-hidden="true">
        <circle cx="12" cy="12" r="9.5" fill="none" stroke="var(--teal-deep)" stroke-width="2"/>
        <path d="M2.5 12h19M12 2.5c3 3 3 16 0 19M12 2.5c-3 3-3 16 0 19" fill="none" stroke="var(--teal-deep)" stroke-width="1.6"/>
      </svg>
      RosalindThorpeGardens.example
    </li>
    <li><span class="icon--plain"></span>Rosalind Thorpe Gardens</li>
    <li><span class="icon--plain"></span>@RosalindThorpeGardens</li>
  </ul>
</section>

</body>
</html>
```